gtw school poster design and change logo name

We already have a logo which only needs to be slightly modified with "school".
We also have two advertising faces, a girl and a boy, which should be on our poster.
Important key data:

bilingual D/E small classes
daycare
private kindergarten
private school from 2024

Poster size: 268,5 x 128 cm
We need logo sizes in different sizes
also for T-shirts.
Attached also a old poster

new clients

0094D4
00A9DD
6FCCEA
C7EBF8
E9F6FB
59FF00
82FF00
B8FF75
E3FFCB
F4FFEA
FFC000
F8CF3A
FAE287
FDF2CF
FEFAEE
F0912C
F2A743
F7CA91
FBE8D2
FDF5EE

```html
<!DOCTYPE html>
<html lang="en">
<head>
<meta charset="utf-8">
<title>gtw school – banner options</title>
<link rel="stylesheet" href="https://fonts.googleapis.com/css2?family=Fredoka:wght@500;600;700&family=Roboto:wght@400;500&display=swap">
<style>
  :root{
    --board:#0a78bb;
    --board-light:#1a8fd2;
    --blue:#1b93d4;
    --blue-deep:#0094D4;
    --sky:#6FCCEA;
    --teal:#1e9bb0;
    --green:#5fb83a;
    --red:#e8393f;
    --yellow:#FFC000;
    --gold:#F8B51C;
    --orange:#F0912C;
    --white:#ffffff;
    --ink:#1d1d1f;
  }
  html,body{margin:0;padding:0;width:1200px;height:1200px;overflow:hidden;background:var(--board);}
  .board{position:relative;width:1280px;height:1280px;transform:scale(0.9375);transform-origin:0 0;background:var(--board);}
  .option-tab{position:absolute;left:0;width:130px;height:104px;display:flex;align-items:center;justify-content:center;font:600 44px/1 "Fredoka",sans-serif;}
  .option-tab--one{top:158px;background:var(--white);color:var(--yellow);}
  .option-tab--two{top:682px;background:var(--yellow);color:var(--white);}
  .option-strip{position:absolute;left:1148px;width:132px;height:104px;background:var(--board-light);}
  .option-strip--one{top:158px;}
  .option-strip--two{top:682px;}
  .banner{position:absolute;left:130px;width:1018px;height:456px;filter:drop-shadow(0 4px 6px rgba(0,0,0,.35));}
  .banner--one{top:158px;}
  .banner--two{top:682px;}
  .banner svg{display:block;width:1018px;height:456px;}
  .headline{font:600 40px "Fredoka",sans-serif;fill:var(--white);letter-spacing:.5px;}
  .bubble-text{font:600 21px "Fredoka",sans-serif;fill:var(--white);}
  .badge-title{font:600 12px "Fredoka",sans-serif;fill:var(--blue-deep);}
  .badge-date{font:600 13px "Fredoka",sans-serif;fill:var(--white);}
  .call-label{font:500 18px "Roboto",sans-serif;fill:var(--ink);}
  .call-number{font:500 25px "Roboto",sans-serif;fill:var(--white);}
  .offer{font:500 20px "Roboto",sans-serif;fill:var(--ink);}
  .offer--small{font-size:15px;}
  .web{font:600 18px "Fredoka",sans-serif;fill:var(--white);letter-spacing:1.5px;}
  .logo-name{font:600 30px "Fredoka",sans-serif;fill:var(--orange);}
  .fill-white{fill:var(--white);}
  .fill-blue{fill:var(--blue);}
  .fill-gold{fill:var(--gold);}
  .fill-red{fill:var(--red);}
  .fill-sky{fill:var(--sky);}
  .fill-green{fill:var(--green);}
  .fill-teal{fill:var(--teal);}
</style>
</head>
<body>
<main class="board">
  <div class="option-tab option-tab--one">1</div>
  <div class="option-strip option-strip--one"></div>
  <div class="option-tab option-tab--two">2</div>
  <div class="option-strip option-strip--two"></div>

  <!-- Option 1 -->
  <section class="banner banner--one">
    <svg viewBox="0 0 1018 456" xmlns="http://www.w3.org/2000/svg">
      <defs>
        <linearGradient id="photoKids1" x1="0" y1="0" x2="1" y2="1">
          <stop offset="0" stop-color="#f3d6c4"/>
          <stop offset=".5" stop-color="#e8b99c"/>
          <stop offset="1" stop-color="#4aa6dc"/>
        </linearGradient>
      </defs>
      <rect class="fill-white" width="1018" height="456"/>
      <path d="M210 0 L255 112 L205 225 L0 225" fill="none" stroke="var(--blue)" stroke-width="2"/>
      <text class="logo-name" x="115" y="130" text-anchor="middle">gtw school</text>

      <polygon class="fill-green" points="230,0 258,0 310,55 258,110 230,110 282,55"/>
      <polygon class="fill-sky" points="262,0 290,0 342,55 290,110 262,110 314,55"/>
      <polygon class="fill-teal" points="294,0 322,0 374,55 322,110 294,110 346,55"/>
      <polygon class="fill-blue" points="330,0 1018,0 1018,105 330,105 378,52"/>
      <text class="headline" x="998" y="68" text-anchor="end">BILINGUAL D/E SMALL CLASSES</text>

      <rect x="560" y="105" width="458" height="351" fill="url(#photoKids1)" role="img" aria-label="Photo of a boy and a girl showing paint-covered hands"/>

      <path d="M560 200 L585 258 L595 205 Z" class="fill-blue" stroke="var(--gold)" stroke-width="2"/>
      <ellipse cx="605" cy="152" rx="85" ry="60" class="fill-blue" stroke="var(--gold)" stroke-width="2"/>
      <text class="bubble-text" x="570" y="136">Do You</text>
      <text class="bubble-text" x="570" y="159">Speak</text>
      <text class="bubble-text" x="570" y="182">English</text>

      <circle cx="920" cy="162" r="66" class="fill-gold"/>
      <circle cx="920" cy="162" r="53" class="fill-white"/>
      <g transform="rotate(35 920 162)">
        <text class="badge-title" x="920" y="158" text-anchor="middle">NEUERÖFFNUNG</text>
        <rect x="874" y="165" width="92" height="20" class="fill-gold"/>
        <text class="badge-date" x="920" y="180" text-anchor="middle">01.02.2018</text>
      </g>

      <polygon class="fill-gold" points="300,160 455,160 440,185 300,185"/>
      <text class="call-label" x="310" y="179">CALL US NOW!</text>
      <polygon class="fill-blue" points="300,185 528,185 505,228 300,228"/>
      <text class="call-number" x="308" y="216">+41 79 555 01 23</text>
      <path d="M250 250 L262 268 L272 240 Z" class="fill-blue" stroke="var(--gold)" stroke-width="3"/>
      <circle cx="250" cy="200" r="42" class="fill-blue" stroke="var(--gold)" stroke-width="4"/>
      <path d="M236 183 c4-3 7-2 9 2 l4 8 c1 3 0 5-2 7 l-3 2 c2 6 7 11 13 13 l2-3 c2-2 4-3 7-2 l8 4 c4 2 5 5 2 9 c-4 5-9 7-15 5 c-14-5-25-16-29-30 c-2-6 0-11 4-15z" class="fill-white"/>

      <rect class="fill-red" x="0" y="285" width="195" height="20"/>
      <rect class="fill-blue" x="0" y="316" width="195" height="20"/>
      <rect class="fill-green" x="0" y="347" width="195" height="20"/>
      <text class="offer" x="213" y="302">DAYCARE</text>
      <text class="offer" x="213" y="333">PRIVATE KINDERGARTEN</text>
      <text class="offer" x="213" y="365">PRIVATE SCHOOL FROM 2024</text>

      <rect class="fill-blue" x="0" y="425" width="560" height="31"/>
      <polygon class="fill-gold" points="195,402 520,402 500,456 215,456"/>
      <text class="web" x="357" y="432" text-anchor="middle">www.gtw-daycare.ch</text>
    </svg>
  </section>

  <!-- Option 2 -->
  <section class="banner banner--two">
    <svg viewBox="0 0 1018 456" xmlns="http://www.w3.org/2000/svg">
      <defs>
        <linearGradient id="photoGirl2" x1="0" y1="0" x2="0" y2="1">
          <stop offset="0" stop-color="#d6b08c"/>
          <stop offset=".6" stop-color="#f3d8c6"/>
          <stop offset="1" stop-color="#e6e6e6"/>
        </linearGradient>
        <linearGradient id="photoBoy2" x1="0" y1="0" x2="0" y2="1">
          <stop offset="0" stop-color="#f0cdb4"/>
          <stop offset=".55" stop-color="#e2b095"/>
          <stop offset="1" stop-color="#3ba3dd"/>
        </linearGradient>
      </defs>
      <rect class="fill-white" width="1018" height="456"/>
      <text class="logo-name" x="130" y="125" text-anchor="middle">gtw school</text>

      <polygon class="fill-green" points="230,0 258,0 310,55 258,110 230,110 282,55"/>
      <polygon class="fill-sky" points="262,0 290,0 342,55 290,110 262,110 314,55"/>
      <polygon class="fill-teal" points="294,0 322,0 374,55 322,110 294,110 346,55"/>
      <polygon class="fill-blue" points="330,0 1018,0 1018,105 330,105 378,52"/>
      <text class="headline" x="998" y="68" text-anchor="end">BILINGUAL D/E SMALL CLASSES</text>

      <rect x="30" y="180" width="300" height="245" fill="url(#photoGirl2)" role="img" aria-label="Photo of a smiling girl showing paint-covered hands"/>
      <rect x="765" y="165" width="253" height="291" fill="url(#photoBoy2)" role="img" aria-label="Photo of a laughing boy showing paint-covered hands"/>

      <path d="M745 190 L775 245 L780 195 Z" class="fill-blue" stroke="var(--gold)" stroke-width="2"/>
      <ellipse cx="770" cy="148" rx="85" ry="58" class="fill-blue" stroke="var(--gold)" stroke-width="2"/>
      <text class="bubble-text" x="733" y="131">Do You</text>
      <text class="bubble-text" x="733" y="154">Speak</text>
      <text class="bubble-text" x="733" y="177">English</text>

      <circle cx="655" cy="228" r="62" class="fill-gold"/>
      <circle cx="655" cy="228" r="50" class="fill-white"/>
      <g transform="rotate(-15 655 228)">
        <text class="badge-title" x="655" y="224" text-anchor="middle">NEUERÖFFNUNG</text>
        <rect x="611" y="231" width="88" height="20" class="fill-gold"/>
        <text class="badge-date" x="655" y="246" text-anchor="middle">01.02.2018</text>
      </g>

      <polygon class="fill-gold" points="350,140 505,140 490,165 350,165"/>
      <text class="call-label" x="362" y="159">CALL US NOW!</text>
      <polygon class="fill-blue" points="350,165 598,165 575,212 350,212"/>
      <text class="call-number" x="358" y="200">+41 79 555 01 23</text>
      <path d="M292 230 L304 250 L314 222 Z" class="fill-blue" stroke="var(--gold)" stroke-width="3"/>
      <circle cx="296" cy="182" r="42" class="fill-blue" stroke="var(--gold)" stroke-width="4"/>
      <path d="M282 165 c4-3 7-2 9 2 l4 8 c1 3 0 5-2 7 l-3 2 c2 6 7 11 13 13 l2-3 c2-2 4-3 7-2 l8 4 c4 2 5 5 2 9 c-4 5-9 7-15 5 c-14-5-25-16-29-30 c-2-6 0-11 4-15z" class="fill-white"/>

      <rect class="fill-red" x="330" y="300" width="180" height="19"/>
      <rect class="fill-blue" x="330" y="332" width="180" height="19"/>
      <rect class="fill-green" x="330" y="363" width="180" height="19"/>
      <text class="offer offer--small" x="528" y="314">DAYCARE</text>
      <text class="offer offer--small" x="528" y="346">PRIVATE KINDERGARTEN</text>
      <text class="offer offer--small" x="528" y="378">PRIVATE SCHOOL FROM 2024</text>

      <rect class="fill-blue" x="0" y="425" width="765" height="31"/>
      <polygon class="fill-gold" points="410,402 750,402 730,456 430,456"/>
      <text class="web" x="580" y="432" text-anchor="middle">www.gtw-daycare.ch</text>
    </svg>
  </section>
</main>
</body>
</html>
```